Powerpoint, Graphics for Sermon Series

I am starting a sermon series on the short letters if Scripture that are between Hebrews and Revelation. The sermon series will be called "Walking Unmarked Trails: Lasting Lessons from Quiet Hills."

Think about finding a packet of letters in an Attic. There is only the dialogue of the writer. We don't know exactly what the receivers were going through or even what their response to the letters were/are!

Target Market(s)

Local Church

Industry/Entity Type

Christian

Font styles to use
Serif
Sans Serif

Colors

Designer to choose colors to be used in the design.

Requirements
Must have
• Powerpoint Slide with Title -
• Background Slide -
• It would be great to have both JPG, PNG, and Photoshop/Indesign that can be used for powerpoint, both in 4x3 ration and wide... Need Title Slide with typography and background slide for text to go over the top of.
• Stick with the theme -- Walking Unmarked Trails
• I am including our church logo, but don't feel like you need to use it in anyway.
Nice to have
• Social Media Slides - Square Slide, Facebook Header
• Greyscale Version?

```html
<!DOCTYPE html>
<html lang="en">
<head>
<meta charset="utf-8">
<title>Walking Unmarked Trails – Text Slide</title>
<link href="https://fonts.googleapis.com/css2?family=Lato:wght@400;700&display=swap" rel="stylesheet">
<style>
  :root {
    --paper-light: #f3efeb;
    --paper-mid: #e9e2db;
    --paper-warm: #ddd3c9;
    --heading: #b24f1c;
    --body: #3d3a38;
    --brand: #5b3b24;
  }
  * { box-sizing: border-box; margin: 0; padding: 0; }
  html, body { width: 1200px; height: 900px; overflow: hidden; }
  body { font-family: "Lato", sans-serif; }
  .slide {
    position: relative;
    width: 1200px;
    height: 900px;
    overflow: hidden;
    background: var(--paper-light);
  }
  .slide__backdrop {
    position: absolute;
    inset: 0;
    background:
      radial-gradient(ellipse at 30% 20%, rgba(255,255,255,0.75), transparent 60%),
      linear-gradient(160deg, var(--paper-light) 0%, var(--paper-mid) 55%, var(--paper-warm) 100%);
  }
  .brand {
    position: absolute;
    top: 40px;
    right: 42px;
    display: flex;
    align-items: center;
    gap: 12px;
    color: var(--brand);
    font-weight: 700;
    font-size: 26px;
    line-height: 1.1;
    text-align: right;
  }
  .brand__mark {
    width: 18px;
    height: 18px;
    background: var(--brand);
  }
  .columns {
    position: absolute;
    top: 182px;
    left: 60px;
    width: 1095px;
    display: grid;
    grid-template-columns: 494px 494px;
    column-gap: 107px;
  }
  .column__title {
    color: var(--heading);
    font-weight: 700;
    font-size: 36px;
    line-height: 46px;
    margin-bottom: 2px;
  }
  .column__body {
    color: var(--body);
    font-size: 21px;
    line-height: 37.5px;
    text-align: justify;
    hyphens: auto;
    -webkit-hyphens: auto;
  }
</style>
</head>
<body>
  <main class="slide">
    <div class="slide__backdrop" role="img" aria-label="Softly faded photograph of an open old book with printed pages"></div>

    <div class="brand">
      <span class="brand__mark"></span>
      <span class="brand__name">Cedar Hollow<br>Community Church</span>
    </div>

    <section class="columns">
      <article class="column">
        <h2 class="column__title">Subtext title here</h2>
        <p class="column__body">Lorem Ipsum is simply dummy text of the printing and typesetting industry. Lorem Ipsum has been the industry's standard dummy text ever since the 1500s, when an unknown printer took a galley of type and scrambled it to make a type specimen book. It has survived not only five centuries, but also the leap into electronic typesetting, remaining essentially unchanged. It was popularised in the 1960s with the release of Letraset sheets contain&shy;ing Lorem Ipsum passages, and more recently with desktop Lorem Ipsum has been the industry's stan&shy;dard dummy text ever since the 1500s, when an unknown printer took a galley of type and scram&shy;bled it to make a type specimen book. It has sur&shy;vived.</p>
      </article>
      <article class="column">
        <h2 class="column__title">Subtext title here</h2>
        <p class="column__body">Lorem Ipsum is simply dummy text of the printing and typesetting industry. Lorem Ipsum has been the industry's standard dummy text ever since the 1500s, when an unknown printer took a galley of type and scrambled it to make a type specimen book. It has survived not only five centuries, but also the leap into electronic typesetting, remaining essentially unchanged. It was popularised in the 1960s with the release of Letraset sheets contain&shy;ing Lorem Ipsum passages, and more recently with desktop Lorem Ipsum has been the industry's stan&shy;dard dummy text ever since the 1500s, when an unknown printer took a galley of type and scram&shy;bled it to make a type specimen book. It has sur&shy;vived.</p>
      </article>
    </section>
  </main>
</body>
</html>
```